IT Company that provides secure IT solutions and services to our customers

We need business cards and a logo for a new IT Solutions company just created based in Kuala Lumpur, Malaysia. But will also be serving other countries in the region. We provide secure data, voice solutions on mobile platforms. Our first offering is encrypted voice and data solutions for IOS, Android, Windows and BlackBerry devices.

Target Market(s)

large organizations Govt, Police, Defence, Anti-corruption, Legal, highly regulated industries such as Health-care, Financial, Banking, Insurance,

Industry/Entity Type

Information Technology

Contact Information for Business Card

VelmoraNet (Logo - colour is ORVEX blue)Roshan Adeel Managing Director Velmora Net Sdn. Bhd.5th Floor, Block D, Wisma PLB,No.14 Jalan Seri Melor,50470, Kuala LumpurMalaysia

Font styles to use
Sans Serif

Colors
3176b5
ec1f27
fbed22

Requirements
Must have
• VelmoraNet all in Blue like ORVEX blue. A logo design perhaps a play of VN, K with a dangling T (colour can be any)
Nice to have
• I want a clean crisp card, not too busy, easy to read.

```html
<!DOCTYPE html>
<html lang="en">
<head>
<meta charset="utf-8">
<title>VelmoraNet Business Cards</title>
<link rel="stylesheet" href="https://fonts.googleapis.com/css2?family=Open+Sans:wght@400;600;700&display=swap">
<style>
  :root {
    --backdrop: #3b3330;
    --card-black: #141414;
    --card-sheen: #262626;
    --brand-blue: #1f5fb8;
    --brand-red: #d9262d;
    --accent-glow: rgba(90, 22, 26, .35);
    --text-white: #f2f2f2;
  }
  * { box-sizing: border-box; margin: 0; padding: 0; }
  html, body {
    width: 1200px; height: 844px; overflow: hidden;
    background: var(--backdrop);
    font-family: "Open Sans", sans-serif;
  }
  .canvas { position: relative; width: 1200px; height: 844px; }
  .card {
    position: absolute; top: 272px;
    width: 520px; height: 300px;
    background: radial-gradient(ellipse at 60% 40%, var(--card-sheen), var(--card-black) 70%);
    overflow: hidden;
    box-shadow: 0 10px 30px rgba(0,0,0,.5);
  }
  .card--front { left: 50px; }
  .card--back { left: 630px; }

  /* front side */
  .band { position: absolute; left: 0; width: 100%; background: var(--brand-blue); }
  .band--top { top: 0; height: 12px; }
  .band--bottom { bottom: 0; height: 16px; }
  .accent-area {
    position: absolute; left: 0; bottom: 16px; width: 100%; height: 90px;
    background: radial-gradient(ellipse at 35% 100%, var(--accent-glow), transparent 70%);
  }

  .contact {
    position: absolute; left: 120px; width: 390px; top: 60px;
    text-align: center; color: var(--text-white);
  }
  .contact__name {
    display: inline-block;
    font-size: 17px; font-weight: 700; letter-spacing: .5px;
    color: var(--brand-blue); text-transform: uppercase;
    padding: 0 6px 2px; border-bottom: 1px solid var(--brand-blue);
  }
  .contact__role { font-size: 12px; margin-top: 2px; }
  .contact__company {
    margin-top: 50px;
    font-size: 15px; font-weight: 700; color: var(--brand-blue);
    text-transform: uppercase;
  }
  .contact__address {
    font-size: 13px; line-height: 1.65; margin-top: 2px; white-space: nowrap;
  }

  /* back side */
  .wordmark {
    position: absolute; left: 0; right: 0; top: 120px;
    text-align: center;
    font-size: 42px; font-weight: 700; color: var(--brand-blue);
  }
  .tab { position: absolute; width: 26px; height: 40px; background: var(--brand-blue); }
  .tab--top-right { right: 0; top: 24px; border-left: 3px solid var(--brand-red); }
  .tab--left { left: 0; top: 200px; border-right: 3px solid var(--brand-red); }
</style>
</head>
<body>
<main class="canvas">
  <section class="card card--front" aria-label="Card front with contact details">
    <div class="band band--top"></div>
    <div class="accent-area" role="img" aria-label="Faint red brand accent area"></div>
    <div class="contact">
      <p class="contact__name">Roshan Adeel</p>
      <p class="contact__role">Managing Director</p>
      <p class="contact__company">Velmora Net</p>
      <p class="contact__address">
        Sdn. Bhd. 5th Floor, Block D, Wisma<br>
        PLB, No.14 Jalan Seri Melor, 50470, Kuala Lumpur Malaysia
      </p>
    </div>
    <div class="band band--bottom"></div>
  </section>

  <section class="card card--back" aria-label="Card back with brand name">
    <div class="tab tab--top-right"></div>
    <p class="wordmark">VelmoraNet</p>
    <div class="tab tab--left"></div>
  </section>
</main>
</body>
</html>
```